Web design for small empirical brand consulting company that will sell a web-based brand tool

We need a totally new and very appealing website:
Purpose: We want to attract lots of potential customers with this website... especially, we want to sell our web-based tool valuquant®... we want to be perceived as innovative, trendy, but solid and reliable… we want customers go to the website, login at „valuquant®“ (see structure), and perceive how it works.. and the contacting us or in the near future being able to buy a login and work with the tool… so we want to a) inform (on the website or send the url to customers) and b) to „force“ potential customers getting in contact with us…
Structure (e.g.): Must Home, valuquant®, About us, Contact (incl. legal notice); we are open for more, Nice to have e.g. references/clients, press... for example, we publish a nice book in a couple of months and might want to show it somewhere on the website as well...)
Layout: We would like to have more/mainly figures - may be animated or something like that – in specific those on slides 7 and 8 as well as 6 and 9 (which would be for our web-based tool valuquant®...)... excellent, but simple and with few text…
Fonts: Eurostile; CMYK 100/23/100/19, CMYK 0/0/0/70
Logo: Would you please use the lorentavo-logo used in this file?
Social Media: we think that it might make sense to be connected to chatterbay, quipline and so on as well…
Phantasy: May be it is possible to have something between a classic marketing research and an e-commerce website... just a thought... because it is mainly about the new tool that will be assessable through a login... but customers might want to contact us or vice versa in order to check how the tool will work (btw: you do not have further info about valuquant® here... I know)… I dream of having a site where people go to and by components of our tool like at brimbo… click and buy and go for it…
It is possible to program it in php or java? Thanks.
Pages I personally like: Don’t know if that helps, but I personally like those websites just they seem so simple: http:// www.pellivarn.com/, http://www.craftelune.net/... but I am veeery open
Pages I do not like anymore: my own www.lorentavo.ch

```html
<!DOCTYPE html>
<html lang="en">
<head>
<meta charset="utf-8">
<title>lorentavo – The statistics-based brand consultancy</title>
<link rel="stylesheet" href="https://fonts.googleapis.com/css2?family=Open+Sans:wght@400;600&family=PT+Sans+Narrow:wght@400;700&display=swap">
<style>
:root{
  --green:#137c40;
  --green-dark:#0f6a36;
  --ink:#4d4d4d;
  --ink-soft:#8a8a8a;
  --line:#e6e6e6;
  --white:#ffffff;
  --night:#0c0c0c;
  --night-2:#161616;
  --paper:#f1f2f2;
}
*{box-sizing:border-box;margin:0;padding:0}
html,body{width:1200px;height:2624px;overflow:hidden}
body{position:relative;background:var(--white);font-family:"Open Sans",Arial,sans-serif;color:var(--ink)}
.abs{position:absolute}

/* header */
.site-header{position:absolute;left:0;top:0;width:1200px;height:95px;background:var(--white)}
.brand{position:absolute;display:flex;align-items:center;gap:8px;font-size:28px;color:var(--ink);letter-spacing:-.5px}
.brand-mark{width:10px;height:24px;background:var(--ink)}
.site-header .brand{left:172px;top:28px}
.main-nav a{position:absolute;top:38px;font-size:16px;color:var(--green);text-decoration:none}

/* hero */
.hero{position:absolute;left:0;top:95px;width:1200px;height:482px;
  background:linear-gradient(90deg,#0d1524 0%,#1c2636 35%,#3d4b5e 60%,#2a3547 80%,#141b28 100%)}
.hero-photo{position:absolute;inset:0;background:radial-gradient(ellipse at 68% 70%,rgba(220,226,235,.55),rgba(0,0,0,0) 45%)}
.hero h1{position:absolute;left:170px;top:140px;width:380px;font-family:"PT Sans Narrow",Arial Narrow,sans-serif;font-weight:400;font-size:36px;line-height:38px;color:var(--white)}
.hero p{position:absolute;left:172px;top:240px;width:334px;font-size:11px;line-height:18px;color:var(--white)}
.hero-arrow{position:absolute;top:240px;width:36px;height:36px;border-radius:50%;background:#111;border:1px solid #555}
.hero-arrow svg{display:block;margin:11px auto}

/* welcome */
.welcome h2{position:absolute;left:0;top:595px;width:1200px;text-align:center;font-weight:400;font-size:27px;color:var(--ink)}
.welcome h2 span{color:var(--green)}
.welcome .lead{position:absolute;left:170px;top:645px;width:860px;text-align:center;font-size:11px;line-height:19px;color:#a5a5a5}
.service-card{position:absolute;top:735px;width:271px;height:270px;border:1px solid var(--line)}
.service-card h3{height:40px;padding:11px 13px;background:var(--green);color:var(--white);font-weight:400;font-size:14px}
.service-card .media{height:144px}
.service-card p{padding:12px 14px;font-size:10.5px;line-height:19px;color:#9a9a9a;text-align:justify}

/* features */
.features{position:absolute;left:0;top:1042px;width:1200px;height:550px;
  background:linear-gradient(135deg,#137c40 0%,#168745 40%,#117539 70%,#158242 100%)}
.feature{position:absolute;width:210px;text-align:center;color:var(--white)}
.feature .ring{width:106px;height:106px;margin:0 auto;border:2px solid rgba(255,255,255,.85);border-radius:50%;display:flex;align-items:center;justify-content:center}
.feature h3{margin-top:26px;font-weight:400;font-size:20px}
.feature p{margin-top:12px;font-size:10.5px;line-height:21px;font-weight:600}

/* press */
.press h2{position:absolute;left:0;top:1617px;width:1200px;text-align:center;font-weight:400;font-size:26px;color:var(--green)}
.press-item{position:absolute;top:1672px;width:274px}
.press-item .media{height:161px}
.press-item .meta{display:flex;height:56px}
.date{width:37px;background:var(--green);color:var(--white);text-align:center;font-size:11px}
.date b{display:block;height:30px;line-height:30px;font-weight:400}
.date i{display:block;font-style:normal;background:#4d4d4d;height:26px;line-height:26px;font-size:10px}
.press-item h3{flex:1;padding:10px 0 0 9px;font-weight:400;font-size:13.5px;line-height:21px;color:var(--ink)}
.press-item p{margin-top:12px;font-size:10.5px;line-height:18px;color:#888}

/* clients */
.clients{position:absolute;left:0;top:2003px;width:1200px;height:187px;background:linear-gradient(#e9ebeb,#f3f4f4 50%,#e4e6e6)}
.clients h2{position:absolute;left:0;top:22px;width:1200px;text-align:center;font-weight:400;font-size:25px;color:#111}
.client-strip{position:absolute;left:171px;top:78px;width:857px;height:82px;background:var(--white);display:flex;align-items:center;justify-content:space-around}
.client{display:flex;align-items:center;gap:8px;font-size:22px;color:#bdbdbd}
.client i{width:22px;height:22px;border-radius:50%;background:#d3d3d3}

/* team & contact */
.team-band{position:absolute;left:0;top:2190px;width:1200px;height:355px;background:linear-gradient(#1d1f21,#0b0b0b)}
.team-band h2{position:absolute;top:20px;font-weight:400;font-size:25px;color:#cfcfcf}
.member{position:absolute;top:84px;width:173px;height:248px;border:1px solid #3a3a3a}
.member .portrait{margin:8px;height:137px;background:linear-gradient(#f2f2f2,#d7cfc8)}
.member p{padding:2px 10px;font-size:10.5px;line-height:23px;color:#aaa}
.contact-box{position:absolute;left:775px;top:84px;width:252px;height:248px;border:1px solid #3a3a3a;padding:12px 20px;color:#aaa;font-size:10.5px;line-height:22px}
.contact-box h3{font-weight:400;font-size:14px;color:#bbb;margin-bottom:14px}
.contact-line{display:flex;align-items:center;gap:12px}
.social{display:flex;gap:26px;margin-top:22px}
.social div{text-align:center;font-size:9px;color:#ddd}
.social span{display:block;width:36px;height:36px;margin:0 auto 2px;border:1px solid #999;border-radius:50%}

/* footer */
.site-footer{position:absolute;left:0;top:2545px;width:1200px;height:79px;background:#1c1c1c}
.site-footer .brand{left:172px;top:24px;color:#bbb;font-size:26px}
.site-footer .brand-mark{background:#bbb}
.site-footer small{position:absolute;left:380px;top:33px;font-size:10px;color:#888}
.to-top{position:absolute;left:987px;top:18px;width:44px;height:44px;border-radius:50%;background:#2c2c2c}
.to-top svg{display:block;margin:16px auto}
</style>
</head>
<body>

<header class="site-header">
  <div class="brand"><span class="brand-mark"></span>lorentavo</div>
  <nav class="main-nav">
    <a style="left:520px" href="#">lorentavo</a>
    <a style="left:656px" href="#">Services</a>
    <a style="left:762px" href="#">Work</a>
    <a style="left:848px" href="#">Credentials</a>
    <a style="left:975px" href="#">Contact</a>
  </nav>
</header>

<section class="hero">
  <div class="hero-photo" role="img" aria-label="Photo of a consulting team working together around a table in a dark office"></div>
  <h1>The statistics-based brand consultancy</h1>
  <p>We are statistically and methodologically trained and experienced excellent. We leave in the areas of brand analysis, brand concept, brand strategy, brand positioning.</p>
  <div class="hero-arrow" style="left:55px"><svg width="12" height="12" viewBox="0 0 12 12"><path d="M8 1 3 6l5 5" fill="none" stroke="#fff" stroke-width="2"/></svg></div>
  <div class="hero-arrow" style="left:1118px"><svg width="12" height="12" viewBox="0 0 12 12"><path d="M4 1l5 5-5 5" fill="none" stroke="#fff" stroke-width="2"/></svg></div>
</section>

<section class="welcome">
  <h2>Welcome To <span>lorentavo</span></h2>
  <p class="lead">Lorem ipsum dolor sit amet, consectetur adipisicing elit. In, sunt illum dolore dolor vel perferendis nisi sequi laudantium porro blanditiis! Lorem ipsum dolor sit amet, consectetur adipisicing elit. In, sunt illum dolore dolor vel perferendis nisi sequi laudantium porro blanditiis! Lorem ipsum dolor sit amet, consectetur adipisicing elit. In, sunt illum dolore dolor vel perferendis nisi sequi laudantium porro blanditiis!</p>
  <article class="service-card" style="left:173px">
    <h3>Company Brand</h3>
    <div class="media" role="img" aria-label="Illustration of colourful gears with teamwork lettering" style="background:linear-gradient(135deg,#1f1f1f,#3a3a3a 60%,#2a2a2a)"></div>
    <p>We are statistically and methodologically trained and experienced excellent. We leave in the areas of brand analysis.</p>
  </article>
  <article class="service-card" style="left:465px">
    <h3>Product &amp; Service</h3>
    <div class="media" role="img" aria-label="Photo of hands holding a glowing clock" style="background:radial-gradient(circle at 50% 45%,#f6b23a,#8a4a10 35%,#1a1208 75%)"></div>
    <p>We are statistically and methodologically trained and experienced excellent. We leave in the areas of brand analysis.</p>
  </article>
  <article class="service-card" style="left:763px">
    <h3>CEO Brand</h3>
    <div class="media" role="img" aria-label="Photo of a businessman touching a digital network of icons" style="background:linear-gradient(135deg,#cfe3f3,#7fa9cf 55%,#d9e8f2)"></div>
    <p>We are statistically and methodologically trained and experienced excellent. We leave in the areas of brand analysis.</p>
  </article>
</section>

<section class="features">
  <div class="feature" style="left:163px;top:40px">
    <div class="ring"><svg width="46" height="46" viewBox="0 0 46 46" fill="#fff"><rect x="4" y="28" width="9" height="16"/><rect x="18" y="18" width="9" height="26"/><rect x="32" y="6" width="9" height="38"/></svg></div>
    <h3>Metrics</h3><p>We are statistically and methodologically trained and experienced excellent. We leave in the areas</p>
  </div>
  <div class="feature" style="left:385px;top:40px">
    <div class="ring"><svg width="50" height="46" viewBox="0 0 50 46" fill="none" stroke="#fff" stroke-width="3"><rect x="3" y="4" width="44" height="28"/><path d="M9 26l9-9 7 6 12-12" /><path d="M19 42h12M25 32v10"/></svg></div>
    <h3>Trend models</h3><p>We are statistically and methodologically trained and experienced excellent. We leave in the areas</p>
  </div>
  <div class="feature" style="left:607px;top:40px">
    <div class="ring"><svg width="52" height="40" viewBox="0 0 52 40" fill="#fff"><circle cx="26" cy="10" r="7"/><path d="M14 36c0-10 5-15 12-15s12 5 12 15z"/><circle cx="10" cy="14" r="5"/><path d="M1 34c0-8 4-11 9-11s8 3 8 11z"/><circle cx="42" cy="14" r="5"/><path d="M34 34c0-8 3-11 8-11s9 3 9 11z"/></svg></div>
    <h3>Precision</h3><p>We are statistically and methodologically trained and experienced excellent. We leave in the areas</p>
  </div>
  <div class="feature" style="left:827px;top:40px">
    <div class="ring"><svg width="50" height="50" viewBox="0 0 50 50" fill="none" stroke="#fff" stroke-width="2.5"><circle cx="25" cy="10" r="7"/><ellipse cx="25" cy="33" rx="17" ry="11"/><path d="M12 42l-2 5M38 42l2 5"/></svg></div>
    <h3>Cost reduction</h3><p>We are statistically and methodologically trained and experienced excellent. We leave in the areas</p>
  </div>

  <div class="feature" style="left:163px;top:287px">
    <div class="ring"><svg width="46" height="46" viewBox="0 0 46 46" fill="#fff"><rect x="3" y="20" width="9" height="22"/><path d="M15 20l8-14c4 0 5 3 4 8h12c3 0 4 3 3 5l-4 18c-1 3-3 5-6 5H15z"/></svg></div>
    <h3>Closeness</h3><p>We are statistically and methodologically trained and experienced excellent. We leave in the areas</p>
  </div>
  <div class="feature" style="left:385px;top:287px">
    <div class="ring"><svg width="40" height="46" viewBox="0 0 40 46"><path d="M10 20v-7a10 10 0 0 1 20 0v7" fill="none" stroke="#fff" stroke-width="4"/><rect x="4" y="20" width="32" height="24" fill="#fff"/><circle cx="20" cy="31" r="4" fill="#168745"/></svg></div>
    <h3>Security</h3><p>We are statistically and methodologically trained and experienced excellent. We leave in the areas</p>
  </div>
  <div class="feature" style="left:607px;top:287px">
    <div class="ring"><svg width="50" height="50" viewBox="0 0 50 50" fill="none" stroke="#fff" stroke-width="3"><circle cx="25" cy="25" r="21"/><path d="M25 11v14l9 6"/></svg></div>
    <h3>Fit</h3><p>We are statistically and methodologically trained and experienced excellent. We leave in the areas</p>
  </div>
  <div class="feature" style="left:827px;top:287px">
    <div class="ring"><svg width="44" height="52" viewBox="0 0 44 52" fill="#fff"><circle cx="20" cy="13" r="10"/><path d="M2 50c0-16 8-24 18-24s18 8 18 24z"/><path d="M20 28l-3 6 3 12 3-12z" fill="#168745"/></svg></div>
    <h3>Customer loyalty</h3><p>We are statistically and methodologically trained and experienced excellent. We leave in the areas</p>
  </div>
</section>

<section class="press">
  <h2>Our press</h2>
  <article class="press-item" style="left:171px">
    <div class="media" role="img" aria-label="Photo of people working on a desk with colour swatches" style="background:linear-gradient(135deg,#dfe3e6,#b9c2c9 50%,#e7e9ea)"></div>
    <div class="meta"><div class="date"><b>15</b><i>Aug</i></div><h3>Neue Talblatt Zeitung: To see other Swiss canton of the train</h3></div>
    <p>Office of the President of the Canton of Riverstadt / External Relations and Marketing - Newsletter 1/13, page 4: Riverstadt: terms of culture.</p>
  </article>
  <article class="press-item" style="left:463px">
    <div class="media" role="img" aria-label="Photo of an engineer in a hard hat in a bright office" style="background:linear-gradient(135deg,#e6f1f6,#bfd9e6 55%,#8fb7cc)"></div>
    <div class="meta"><div class="date"><b>15</b><i>Aug</i></div><h3>Neue Talblatt Zeitung: To see other Swiss canton of the train</h3></div>
    <p>Office of the President of the Canton of Riverstadt / External Relations and Marketing - Newsletter 1/13, page 4: Riverstadt: terms of culture.</p>
  </article>
  <article class="press-item" style="left:757px">
    <div class="media" role="img" aria-label="Photo of two businessmen facing a chalkboard with search marketing sketches" style="background:radial-gradient(circle at 45% 40%,#d8d2c2,#6e6a62 45%,#3a3a38)"></div>
    <div class="meta"><div class="date"><b>15</b><i>Aug</i></div><h3>Neue Talblatt Zeitung: To see other Swiss canton of the train</h3></div>
    <p>Office of the President of the Canton of Riverstadt / External Relations and Marketing - Newsletter 1/13, page 4: Riverstadt: terms of culture.</p>
  </article>
</section>

<section class="clients">
  <h2>Client Benefits</h2>
  <div class="client-strip">
    <div class="client"><i></i>Gravelo</div>
    <div class="client"><i></i>Nimbara</div>
    <div class="client"><i></i>Pontix</div>
    <div class="client">Amberlane</div>
    <div class="client"><i></i>Quellor</div>
  </div>
</section>

<section class="team-band">
  <h2 style="left:172px">Our Team</h2>
  <h2 style="left:775px">Contact us</h2>
  <div class="member" style="left:171px">
    <div class="portrait" role="img" aria-label="Portrait photo of a team member"></div>
    <p>Dr. Anton Weber<br>Lindholm University<br>Business Psychology<br>Phone: +41 00 555 01 20</p>
  </div>
  <div class="member" style="left:369px">
    <div class="portrait" role="img" aria-label="Portrait photo of a team member"></div>
    <p>Dr. Anton Weber<br>Lindholm University<br>Business Psychology<br>Phone: +41 00 555 01 20</p>
  </div>
  <div class="member" style="left:565px">
    <div class="portrait" role="img" aria-label="Portrait photo of a team member"></div>
    <p>Dr. Anton Weber<br>Lindholm University<br>Business Psychology<br>Phone: +41 00 555 01 20</p>
  </div>
  <div class="contact-box">
    <h3>Corporate Office</h3>
    <p>Lorentavo ltd. Weidenweg 14<br>CH - 8000 Musterdorf</p>
    <div class="contact-line" style="margin-top:10px"><svg width="16" height="16" viewBox="0 0 16 16"><path d="M3 1l3 3-2 2c1 3 3 5 6 6l2-2 3 3-2 2C7 15 1 9 1 3z" fill="none" stroke="#aaa" stroke-width="1.3"/></svg>+41 00 555 02 83</div>
    <div class="contact-line"><svg width="16" height="12" viewBox="0 0 16 12"><rect x=".7" y=".7" width="14.6" height="10.6" fill="none" stroke="#aaa" stroke-width="1.3"/><path d="M1 1l7 6 7-6" fill="none" stroke="#aaa" stroke-width="1.3"/></svg>t.maurer@lorentavo.ch</div>
    <div class="social">
      <div><span></span>chatterbay</div>
      <div><span></span>quipline</div>
      <div><span></span>plusora</div>
    </div>
  </div>
</section>

<footer class="site-footer">
  <div class="brand"><span class="brand-mark"></span>lorentavo</div>
  <small>© 2013 lorentavo All rights reserved.</small>
  <div class="to-top"><svg width="12" height="8" viewBox="0 0 12 8"><path d="M1 7l5-5 5 5" fill="none" stroke="#777" stroke-width="2"/></svg></div>
</footer>

</body>
</html>
```